Medical VIP club - small design

Please read the specs in a design brief attached. Also we don't have logo in a Vector format and attaching the only version we have.

Club

```html
<!DOCTYPE html>
<html lang="en">
<head>
<meta charset="utf-8">
<title>Healvia — VIP Club</title>
<link rel="stylesheet" href="https://fonts.googleapis.com/css2?family=Arimo:wght@400;700&family=PT+Sans:wght@400;700&display=swap">
<style>
:root{
  --page:#6d5e4b;
  --panel-top:#e7e1d6;
  --panel-bot:#9c8d76;
  --frame:#f3efe7;
  --tab-top:#d6cdbf;
  --tab-bot:#8e7e67;
  --tab-active-top:#efd566;
  --tab-active-bot:#b8960f;
  --brand:#5a4a34;
  --gold:#f0c43c;
  --white:#ffffff;
  --ink:#2f281f;
}
*{box-sizing:border-box;margin:0;padding:0}
html,body{width:1200px;height:1036px;overflow:hidden}
body{background:var(--page);font-family:Arimo,Arial,sans-serif;position:relative}
.site-header{position:absolute;left:23px;top:10px;width:1160px;height:187px;border:2px solid var(--frame);border-radius:14px;overflow:hidden;background:linear-gradient(180deg,var(--panel-top),var(--panel-bot))}
.brand{position:absolute;left:32px;top:60px;display:flex;align-items:center;gap:12px}
.brand-mark{width:30px;height:30px;border-radius:50%;background:var(--brand)}
.brand-name{font-family:Arimo,Arial,sans-serif;font-weight:700;font-size:52px;color:var(--brand);letter-spacing:-1px}
.header-scene{position:absolute;left:455px;top:0;right:0;bottom:0;background:linear-gradient(100deg,rgba(0,0,0,0) 0%,#5e9db4 18%,#4f8aa0 45%,#7a9a6a 70%,#5b7a4c 100%)}
.phone-badge{position:absolute;left:765px;top:52px;width:104px;height:104px;border-radius:50%;background:radial-gradient(circle at 40% 35%,#e1c07a,#8c6626 70%);border:3px solid #f1e6c8}
.phone-badge svg{position:absolute;left:24px;top:24px}
.phone-number{position:absolute;left:912px;top:76px;font-family:Arimo,Arial,sans-serif;font-weight:700;font-size:42px;color:var(--white);text-shadow:0 0 3px #3b2e1c,1px 2px 2px #3b2e1c}
.nav-band{position:absolute;left:0;top:240px;width:1200px;height:38px;background:linear-gradient(180deg,#efe8db,#c9bca6)}
.main-nav{position:absolute;left:24px;top:207px;display:flex;gap:3.5px}
.main-nav a{display:flex;align-items:center;justify-content:center;width:190px;height:71px;border-radius:14px 14px 0 0;background:linear-gradient(180deg,var(--tab-top),var(--tab-bot));color:var(--white);font-size:20px;text-decoration:none;border:1px solid #e9e2d6;border-bottom:none}
.main-nav a.is-active{background:linear-gradient(180deg,var(--tab-active-top),var(--tab-active-bot))}
.nav-rule{position:absolute;left:0;top:278px;width:1200px;height:2px;background:#f2ece1}
.hero{position:absolute;left:22px;top:291px;width:1163px;height:418px;border:2px solid var(--frame);border-radius:14px;overflow:hidden;background:linear-gradient(180deg,#7a5a34 0%,#b88a4e 35%,#9e7650 65%,#5b4530 100%)}
.hero-arrow{position:absolute;top:186px}
.hero-arrow.prev{left:20px}
.hero-arrow.next{right:14px}
.hero-title{position:absolute;left:680px;top:220px;font-family:"PT Sans",sans-serif;font-size:90px;color:#857560;-webkit-text-stroke:2px #f4efe4;text-shadow:2px 3px 4px rgba(0,0,0,.5);line-height:1}
.hero-text{position:absolute;left:708px;top:325px;width:370px;font-family:Arimo,Arial,sans-serif;font-weight:700;font-size:20px;line-height:28px;color:var(--white)}
.feature-tiles{position:absolute;left:23px;top:719px;display:flex;gap:8px}
.feature-tile{width:227px;height:210px;border:2px solid var(--frame);border-radius:12px}
.tile-hospital{background:linear-gradient(135deg,#2f6fc0,#d8e3ef 60%,#8aa7c8)}
.tile-travel{background:linear-gradient(135deg,#0b58c8,#3b8ae6 55%,#0a3f9c)}
.tile-resort{background:linear-gradient(180deg,#78b7e6,#e9ece8 45%,#7e8f6b)}
.tile-staff{background:linear-gradient(180deg,#f5f6f8,#dfe7f0 60%,#b9c8dc)}
.tile-membership{background:linear-gradient(135deg,#dce7f4,#f7f9fc 50%,#b5c7de)}
.site-footer{position:absolute;left:18px;top:940px;width:1170px;height:84px;border:2px solid var(--frame);border-radius:14px;background:linear-gradient(180deg,var(--panel-top),var(--panel-bot))}
.social{position:absolute;left:26px;top:26px;display:flex;gap:6px}
.social span{width:36px;height:36px;border-radius:5px;display:block}
.social .s1{background:#3b5a9a}
.social .s2{background:#49b6e2}
.social .s3{background:#e8641e}
.copyright{position:absolute;left:0;right:0;top:36px;text-align:center;font-size:12px;color:var(--ink)}
.footer-brand{position:absolute;right:30px;top:20px;display:flex;align-items:center;gap:8px}
.footer-brand .brand-mark{width:22px;height:22px}
.footer-brand .brand-name{font-size:36px}
</style>
</head>
<body>
<header class="site-header">
  <div class="header-scene" role="img" aria-label="Coastal beach and sea view"></div>
  <div class="brand"><span class="brand-mark"></span><span class="brand-name">Healvia</span></div>
  <div class="phone-badge">
    <svg width="56" height="56" viewBox="0 0 56 56"><path d="M6 22c0-8 10-12 22-12s22 4 22 12v4h-10v-5c-4-2-20-2-24 0v5H6z" fill="#fff"/><path d="M14 30h28l4 16H10z" fill="#fff"/><circle cx="28" cy="37" r="5" fill="#a07a35"/></svg>
  </div>
  <div class="phone-number">555-010-010</div>
</header>

<div class="nav-band"></div>
<nav class="main-nav">
  <a href="#">About Us</a>
  <a href="#">VIP Club</a>
  <a href="#">Services</a>
  <a href="#">Packages &amp; Prices</a>
  <a href="#" class="is-active">Registration</a>
  <a href="#">Contacts</a>
</nav>
<div class="nav-rule"></div>

<section class="hero" role="img" aria-label="Grand marble hall with crystal chandeliers">
  <svg class="hero-arrow prev" width="58" height="68" viewBox="0 0 58 68"><path d="M56 0L0 34l56 34-16-34z" fill="var(--gold)"/></svg>
  <svg class="hero-arrow next" width="58" height="68" viewBox="0 0 58 68"><path d="M2 0l56 34L2 68l16-34z" fill="var(--gold)"/></svg>
  <h1 class="hero-title">VIP Club</h1>
  <p class="hero-text">Lorem ipsum dolor. Lorem ipsum dolor. Lorem ipsum dolor...</p>
</section>

<div class="feature-tiles">
  <div class="feature-tile tile-hospital" role="img" aria-label="Hospital building with emergency sign"></div>
  <div class="feature-tile tile-travel" role="img" aria-label="Airplanes over a world map"></div>
  <div class="feature-tile tile-resort" role="img" aria-label="Couple on a seaside resort terrace"></div>
  <div class="feature-tile tile-staff" role="img" aria-label="Team of medical staff"></div>
  <div class="feature-tile tile-membership" role="img" aria-label="Membership terms document with pen"></div>
</div>

<footer class="site-footer">
  <div class="social"><span class="s1"></span><span class="s2"></span><span class="s3"></span></div>
  <p class="copyright">Copyright ©2010 Healvia. All Rights Reserved</p>
  <div class="footer-brand"><span class="brand-mark"></span><span class="brand-name">Healvia</span></div>
</footer>
</body>
</html>
```